Kestrada LLC, needs a web page no more than 5 pages (for now)

Kestrada is a general contractor. Our services include general contracting, design-build construction, disaster recovery and environmental remediation. Our main clients are PMX, TQ, State and Local Gov't Agencies, Hospitals and Schools. Kestrada is also a SDVOSB.

```html
<!DOCTYPE html>
<html lang="en">
<head>
<meta charset="utf-8">
<title>Kestrada — General Contractor</title>
<link href="https://fonts.googleapis.com/css2?family=Poppins:wght@400;500;600;700&display=swap" rel="stylesheet">
<style>
:root{
  --black:#000;
  --panel:#0c0c0c;
  --band:#1b1b1b;
  --gold:#c8923a;
  --gold-light:#e2ad4c;
  --bronze:#a8722c;
  --white:#fff;
  --muted:#d8d8d8;
  --badge:#34455f;
}
*{margin:0;padding:0;box-sizing:border-box}
html,body{width:1200px;height:3707px;overflow:hidden;background:var(--black)}
body{position:relative;font-family:'Poppins',sans-serif;color:var(--white)}
.abs{position:absolute}
.backdrop{position:absolute;left:0;top:0}
.hero-photo{left:0;top:0;width:1200px;height:720px;
  background:radial-gradient(ellipse 420px 420px at 330px 260px,#a0714a 0%,#6a4a33 35%,transparent 70%),
  linear-gradient(100deg,#c97a1e 0%,#5e4632 30%,#2a2623 60%,#171615 100%)}
.nav a{position:absolute;color:var(--white);text-decoration:none;font-size:14px;font-weight:400;top:53px}
.nav .home{left:142px;top:40px;width:85px;height:42px;line-height:42px;text-align:center;
  background:linear-gradient(90deg,#b27a34,#d9a860);border-radius:2px}
.brand{display:flex;align-items:center;gap:10px;color:var(--gold-light);font-weight:500;font-size:30px;letter-spacing:2px}
.brand .dot{width:16px;height:16px;border-radius:50%;background:var(--gold-light)}
.hero-title{left:607px;top:266px;font-size:39px;line-height:46px;font-weight:700;text-transform:uppercase}
.hero-text{left:607px;top:374px;width:430px;font-size:14.5px;line-height:24px}
.btn{display:block;text-align:center;color:#111;font-weight:600;text-decoration:none;
  background:linear-gradient(90deg,#b07632,#deb06a);border-radius:4px}
.scroll{top:222px;font-size:12px;transform:rotate(90deg);transform-origin:left top;left:1117px}
.vline{width:1px;background:#666;left:600px}
.section-title{font-size:37px;font-weight:700;text-transform:uppercase;text-align:center}
.section-title .lead{color:var(--bronze)}
.section-title .key{color:var(--gold-light)}
.card{width:218px;height:235px;top:863px;border:1.5px solid var(--gold);border-radius:8px;
  text-align:center;padding:18px 14px 0;background:rgba(0,0,0,.35)}
.card svg{width:58px;height:58px}
.card h3{color:var(--gold-light);font-size:15px;line-height:19px;font-weight:700;text-transform:uppercase;margin-top:10px}
.card p{font-size:12.5px;line-height:15.5px;margin-top:14px}
.body-text{font-size:15px;line-height:19.5px;text-align:center}
.client{width:200px;text-align:center}
.client .photo{width:187px;height:187px;border-radius:50%;margin:0 auto;border:2px solid #2f6fc0}
.client .badge{background:var(--badge)}
.client span{display:block;color:var(--gold-light);font-size:17px;line-height:20px;margin-top:14px}
.why h4{color:var(--gold-light);font-size:14px;font-weight:700;margin-bottom:14px}
.why p{font-size:15px;line-height:20px;margin-bottom:22px}
.footer-nav a{color:var(--white);text-decoration:none;font-size:15px;margin:0 11px}
.social{width:42px;height:42px;border-radius:50%;border:2px solid var(--gold);display:block}
</style>
</head>
<body>

<div class="abs hero-photo" role="img" aria-label="Smiling construction worker in an orange hard hat and glasses, on-site background"></div>

<svg class="backdrop" width="1200" height="3707" viewBox="0 0 1200 3707" aria-hidden="true">
  <defs>
    <linearGradient id="goldline" x1="0" x2="1">
      <stop offset="0" stop-color="#6b4a1e"/><stop offset=".5" stop-color="#f0c060"/><stop offset="1" stop-color="#6b4a1e"/>
    </linearGradient>
  </defs>
  <polygon points="470,0 780,0 600,162" fill="#000" opacity=".85"/>
  <polygon points="0,547 600,720 1200,547 1200,1094 600,1266 0,1094" fill="var(--panel)"/>
  <polygon points="0,547 600,720 1200,547 1200,551 600,730 0,551" fill="url(#goldline)"/>
  <polygon points="0,1094 600,1266 1200,1094 1200,1098 600,1276 0,1098" fill="url(#goldline)"/>
  <polygon points="0,1780 1200,1780 1200,2170 600,2345 0,2170" fill="var(--band)"/>
  <polygon points="0,2170 600,2345 1200,2170 1200,2174 600,2355 0,2174" fill="url(#goldline)"/>
  <polygon points="0,2914 1200,2914 1200,3202 600,3374 0,3202" fill="#141414"/>
  <polygon points="0,3202 600,3374 1200,3202 1200,3206 600,3384 0,3206" fill="url(#goldline)"/>
</svg>

<nav class="nav">
  <a class="home" href="#">Home</a>
  <a href="#" style="left:240px">About Us</a>
  <a href="#" style="left:328px">Why Kestrada?</a>
  <a href="#" style="left:777px">Services</a>
  <a href="#" style="left:860px">Who we serve</a>
  <a href="#" style="left:983px">Contact Us</a>
</nav>
<div class="abs brand" style="left:488px;top:48px">KESTRADA<span class="dot"></span></div>

<h1 class="abs hero-title">Kestrada is a<br>general contractor</h1>
<p class="abs hero-text">Our services include general contracting, design-build construction, disaster recovery and environmental remediation</p>
<a class="abs btn" href="#" style="left:604px;top:470px;width:160px;height:42px;line-height:42px;font-size:18px">Contact Us</a>
<div class="abs scroll">Scroll</div>
<div class="abs vline" style="left:1111px;top:266px;height:108px;background:#c8923a"></div>
<div class="abs vline" style="top:640px;height:70px"></div>

<h2 class="abs section-title" style="left:0;width:1200px;top:796px"><span class="lead">Our </span><span class="key">Services</span></h2>

<div class="abs card" style="left:138px">
  <svg viewBox="0 0 60 60" fill="none" stroke="#fff" stroke-width="2"><rect x="10" y="8" width="30" height="42" rx="2"/><path d="M16 20h18M16 28h18M16 36h12"/><path d="M36 40l14-14 4 4-14 14-6 2z"/></svg>
  <h3>General<br>Contracting</h3>
  <p>Reliable, end-to-end project management ensuring quality, safety, and on-time delivery.</p>
</div>
<div class="abs card" style="left:374px">
  <svg viewBox="0 0 60 60" fill="none" stroke="#fff" stroke-width="2"><rect x="8" y="8" width="40" height="44"/><path d="M18 34l12-10 12 10v12H18z"/><circle cx="48" cy="46" r="7"/></svg>
  <h3>Design-Build<br>Construction</h3>
  <p>Streamlined design and construction integration for cost efficiency, speed, and innovation.</p>
</div>
<div class="abs card" style="left:610px">
  <svg viewBox="0 0 60 60" fill="none" stroke="#fff" stroke-width="2"><path d="M8 50V20h22v30M12 26h6M12 34h6M22 26h4M22 34h4"/><path d="M30 50V30h12"/><circle cx="44" cy="42" r="9"/><path d="M44 12c4 6 6 9 6 12a6 6 0 0 1-12 0c0-3 2-6 6-12z"/></svg>
  <h3>Disaster<br>Recovery</h3>
  <p>Rapid response and recovery services to restore essential operations after natural or man-made disasters.</p>
</div>
<div class="abs card" style="left:846px">
  <svg viewBox="0 0 60 60" fill="none" stroke="#fff" stroke-width="2"><circle cx="30" cy="30" r="20"/><path d="M18 48V30h10v18M32 48V24h10v24"/><path d="M12 18a22 22 0 0 1 30-8M48 40a22 22 0 0 1-26 12"/></svg>
  <h3>Environmental<br>Remediation</h3>
  <p>Safe, compliant cleanup and remediation services that protect people, infrastructure, and the environment.</p>
</div>

<div class="abs vline" style="top:1194px;height:123px"></div>

<h2 class="abs section-title" style="left:148px;width:416px;top:1368px"><span class="lead">About </span><span class="key">Us</span></h2>
<p class="abs body-text" style="left:148px;width:416px;top:1437px">Kestrada is a Service-Disabled Veteran-Owned Small Business (SDVOSB) delivering trusted, results-driven construction solutions. With a focus on integrity, precision, and resilience, we partner with government agencies, healthcare institutions, and educational organizations to create lasting impact.</p>
<a class="abs btn" href="#" style="left:276px;top:1578px;width:160px;height:42px;line-height:42px;font-size:15px">Read more</a>

<svg class="abs" style="left:626px;top:1317px" width="404" height="380" viewBox="0 0 404 380" role="img" aria-label="Construction worker in a hard hat viewing a building under construction">
  <defs><linearGradient id="aboutPhoto" x1="0" y1="0" x2="1" y2="1"><stop offset="0" stop-color="#d9e4f4"/><stop offset=".45" stop-color="#8a5cc4"/><stop offset=".7" stop-color="#d77a24"/><stop offset="1" stop-color="#1f3d6e"/></linearGradient></defs>
  <path transform="translate(-6,6)" d="M236,6 C336,0 402,72 400,172 C398,272 332,362 222,372 C122,380 40,330 30,262 C20,194 70,160 92,100 C114,40 166,10 236,6 Z" fill="#c8923a"/>
  <path d="M236,6 C336,0 402,72 400,172 C398,272 332,362 222,372 C122,380 40,330 30,262 C20,194 70,160 92,100 C114,40 166,10 236,6 Z" fill="url(#aboutPhoto)"/>
</svg>

<div class="abs vline" style="top:1688px;height:92px"></div>

<h2 class="abs section-title" style="left:0;width:1200px;top:1825px"><span class="lead">Who we </span><span class="key">Serve</span></h2>
<p class="abs" style="left:0;width:1200px;top:1884px;text-align:center;color:var(--gold-light);font-size:17px">Our expertise supports organizations where reliability is mission-critical</p>

<div class="abs client" style="left:135px;top:1964px">
  <div class="photo badge" role="img" aria-label="Agency badge placeholder"></div>
  <span>PMX</span>
</div>
<div class="abs client" style="left:383px;top:1964px">
  <div class="photo" role="img" aria-label="Blue folder with house keys" style="background:linear-gradient(160deg,#5a3a34 0%,#1e3f9a 35%,#163080 100%)"></div>
  <span>TQ</span>
</div>
<div class="abs client" style="left:622px;top:1964px">
  <div class="photo" role="img" aria-label="Two professionals walking in an office" style="background:linear-gradient(180deg,#cfd8e0 0%,#6b7f96 55%,#2c3a55 100%)"></div>
  <span>State &amp; Local<br>Government Agencies</span>
</div>
<div class="abs client" style="left:867px;top:1964px">
  <div class="photo" role="img" aria-label="Stethoscope resting on a flag" style="background:linear-gradient(160deg,#1c2f6e 0%,#e8e8ee 50%,#b8202c 100%)"></div>
  <span>Hospitals &amp;<br>Healthcare Systems</span>
</div>

<div class="abs vline" style="top:2280px;height:123px"></div>

<h2 class="abs section-title" style="left:138px;top:2426px;text-align:left"><span class="lead">Why </span><span class="key">Kestrada?</span></h2>
<div class="abs why" style="left:143px;top:2500px;width:440px">
  <h4>Veteran-Led, Mission-Focused</h4>
  <p>We bring discipline, leadership, and accountability from the military to every project.</p>
  <h4>Proven Experience</h4>
  <p>Trusted by federal, state, and local agencies on high-stakes projects.</p>
  <h4>Resilient Solutions</h4>
  <p>Built to perform, recover, and endure.</p>
</div>

<svg class="abs" style="left:626px;top:2404px" width="404" height="380" viewBox="0 0 404 380" role="img" aria-label="Smiling construction worker in a safety vest holding a phone">
  <defs><linearGradient id="whyPhoto" x1="0" y1="0" x2="1" y2="1"><stop offset="0" stop-color="#e9ecef"/><stop offset=".4" stop-color="#8c6a55"/><stop offset=".7" stop-color="#d8662a"/><stop offset="1" stop-color="#3c3c38"/></linearGradient></defs>
  <path transform="translate(-6,6)" d="M236,6 C336,0 402,72 400,172 C398,272 332,362 222,372 C122,380 40,330 30,262 C20,194 70,160 92,100 C114,40 166,10 236,6 Z" fill="#c8923a"/>
  <path d="M236,6 C336,0 402,72 400,172 C398,272 332,362 222,372 C122,380 40,330 30,262 C20,194 70,160 92,100 C114,40 166,10 236,6 Z" fill="url(#whyPhoto)"/>
</svg>

<div class="abs vline" style="top:2866px;height:48px"></div>

<h2 class="abs section-title" style="left:0;width:1200px;top:3056px"><span class="lead">Partner with </span><span class="key">Kestrada</span></h2>
<p class="abs" style="left:0;width:1200px;top:3112px;text-align:center;font-size:27px">Where mission, quality, and resilience meet.</p>
<a class="abs btn" href="#" style="left:505px;top:3197px;width:190px;height:42px;line-height:42px;font-size:16px">Contact Us Today</a>

<div class="abs brand" style="left:488px;top:3450px">KESTRADA<span class="dot"></span></div>
<nav class="abs footer-nav" style="left:0;width:1200px;top:3552px;text-align:center">
  <a href="#">Home</a><a href="#">About Us</a><a href="#">Why Kestrada?</a><a href="#">Services</a><a href="#">Who we serve</a><a href="#">Contact Us</a>
</nav>
<div class="abs" style="left:493px;top:3602px;display:flex;gap:15px">
  <a class="social" href="#" aria-label="Social link 1"></a><a class="social" href="#" aria-label="Social link 2"></a><a class="social" href="#" aria-label="Social link 3"></a><a class="social" href="#" aria-label="Social link 4"></a>
</div>
<p class="abs" style="left:0;width:1200px;top:3664px;text-align:center;font-size:12px">© 2025 | www.kestrada.com</p>

</body>
</html>
```